Brightwater Care Partners, LLC Business Card update!

would like a classier business card. Our cards currently just have our logo and contact information. Need better use of color and creativity
Logo attached.

Target Market(s)

Potential clients, contacts, existing clients. We are a consulting company

Industry/Entity Type

Business

Contact Information for Business Card

We like our colors but just have a boring card with our logo and a white background. I want something that stands out.

Colors
ec1f27
757575

Requirements
Must have
• Color to stay consistent. Logo provided
Nice to have
• Just better use of color/ design

```html
<!DOCTYPE html>
<html lang="en">
<head>
<meta charset="utf-8">
<title>Brightwater Care Partners – Business Card</title>
<link href="https://fonts.googleapis.com/css2?family=Open+Sans:ital,wght@0,400;0,600;0,700;1,400&display=swap" rel="stylesheet">
<style>
  :root {
    --brand-red: #ec1f27;
    --brand-red-deep: #c1272d;
    --brand-grey: #757575;
    --stripe-grey: #b3b5b7;
    --rule-grey: #c8c8c8;
    --ink: #1a1a1a;
    --paper: #ffffff;
    --backdrop: #1c1c1c;
  }
  * { box-sizing: border-box; margin: 0; padding: 0; }
  html, body {
    width: 1200px;
    height: 900px;
    overflow: hidden;
    background: var(--backdrop);
    font-family: "Open Sans", Arial, sans-serif;
  }
  .business-card {
    position: absolute;
    left: 180px;
    top: 210px;
    width: 840px;
    height: 480px;
    background: var(--paper);
    overflow: hidden;
  }
  .corner-accent {
    position: absolute;
    left: 0;
    top: 0;
    width: 840px;
    height: 480px;
  }
  .header-rule {
    position: absolute;
    left: 290px;
    top: 70px;
    width: 500px;
    height: 1px;
    background: var(--rule-grey);
  }
  .owner {
    position: absolute;
    left: 60px;
    top: 70px;
  }
  .owner-name {
    font-weight: 700;
    font-size: 27px;
    color: var(--ink);
    line-height: 1.1;
  }
  .owner-title {
    font-style: italic;
    font-size: 21px;
    color: var(--brand-red);
    margin-top: 2px;
  }
  .brand {
    position: absolute;
    right: 50px;
    top: 100px;
    display: flex;
    align-items: center;
    gap: 20px;
  }
  .brand-mark {
    width: 44px;
    height: 44px;
    background: var(--brand-red);
    flex: none;
  }
  .brand-name {
    font-size: 40px;
    font-weight: 600;
    color: var(--brand-grey);
    line-height: 1.05;
    text-align: left;
  }
  .contact-list {
    position: absolute;
    right: 36px;
    top: 232px;
    list-style: none;
    text-align: right;
  }
  .contact-item {
    display: flex;
    justify-content: flex-end;
    align-items: center;
    gap: 16px;
    font-size: 20px;
    color: var(--ink);
    line-height: 33px;
  }
  .contact-icon {
    width: 16px;
    height: 16px;
    flex: none;
    fill: var(--brand-red);
  }
  .contact-item.address { gap: 0; padding-right: 32px; }
</style>
</head>
<body>
  <main class="business-card">
    <svg class="corner-accent" viewBox="0 0 840 480" aria-hidden="true">
      <polygon points="0,238 0,262 262,480 300,480" fill="var(--stripe-grey)"/>
      <polygon points="0,262 0,480 262,480" fill="var(--brand-red-deep)"/>
    </svg>

    <div class="header-rule"></div>

    <div class="owner">
      <p class="owner-name">Owner Name</p>
      <p class="owner-title">Managing Director</p>
    </div>

    <div class="brand">
      <span class="brand-mark"></span>
      <p class="brand-name">Brightwater<br>Care Partners</p>
    </div>

    <ul class="contact-list">
      <li class="contact-item">000 123 456 456
        <svg class="contact-icon" viewBox="0 0 16 16"><path d="M3 1h3l1.5 4-2 1.3a9 9 0 0 0 4.2 4.2L11 8.5l4 1.5v3a2 2 0 0 1-2 2A12 12 0 0 1 1 3a2 2 0 0 1 2-2z"/></svg>
      </li>
      <li class="contact-item">info@companyname.com
        <svg class="contact-icon" viewBox="0 0 16 16"><path d="M1 3h14v10H1z M1.5 3.5 8 9l6.5-5.5" stroke="#fff" stroke-width="1.2"/></svg>
      </li>
      <li class="contact-item">www.companyname.com
        <svg class="contact-icon" viewBox="0 0 16 16"><path d="M6.5 9.5l3-3M7 4.5l1.5-1.5a2.8 2.8 0 0 1 4 4L11 8.5M9 11.5 7.5 13a2.8 2.8 0 0 1-4-4L5 7.5" fill="none" stroke="var(--brand-red)" stroke-width="2" stroke-linecap="round"/></svg>
      </li>
      <li class="contact-item">Address line1, Address Line, country, 012
        <svg class="contact-icon" viewBox="0 0 16 16"><path d="M8 1a5 5 0 0 1 5 5c0 4-5 9-5 9S3 10 3 6a5 5 0 0 1 5-5zm0 3a2 2 0 1 0 0 4 2 2 0 0 0 0-4z"/></svg>
      </li>
    </ul>
  </main>
</body>
</html>
```